Modern Neon Office Sign that says Light Warrior

I want a design for a neon sign in my office. Two lines, the first line that says 'light', and the second line says 'warrior' both centered. I would like 'light' in a script and 'warrior' in a bold font both that would look good in neon. I want the script to be continuous, perhaps with the first letter separated, and the second line warrior to be in a bold custom font that would look good in neon. The script should be playful and easy to read. The word warrior should be bold, and a custom font in some way that looks like it was deigned for the purpose of a neon sign.
Target Market(s)
this is for my office for a neon sign
Industry/Entity Type
personal
Colors
Designer to choose only greyscale colors for use in the design.
Requirements
Must have
- two line sign with script on top and bold print on bottom
Nice to have
- the script should be custom
Should not have
- too many colors - the sign will be white

```html
<!DOCTYPE html>
<html lang="en">
<head>
<meta charset="UTF-8">
<title>Light Warrior – Neon Sign</title>
<link rel="stylesheet" href="https://fonts.googleapis.com/css2?family=Yellowtail&family=Damion&family=Montserrat:wght@800&display=block">
<style>
  :root {
    --backdrop: #141212;
    --neon-core: #ffffff;
    --neon-edge: #fff6cf;
    --neon-glow: rgba(255, 250, 230, 0.8);
    --neon-halo: rgba(255, 245, 225, 0.35);
  }
  html, body {
    margin: 0;
    padding: 0;
    width: 1200px;
    height: 1200px;
    overflow: hidden;
    background: var(--backdrop);
  }
  .sign {
    position: relative;
    width: 1200px;
    height: 1200px;
  }
  .script-line {
    position: absolute;
    left: 0;
    width: 1204px;
    top: 228px;
    margin: 0;
    text-align: center;
    font-family: "Yellowtail", "Damion", cursive;
    font-weight: 400;
    font-size: 330px;
    line-height: 1;
    color: var(--neon-core);
    -webkit-text-stroke: 2px var(--neon-edge);
    text-shadow:
      0 0 4px var(--neon-glow),
      0 0 14px var(--neon-glow),
      0 0 40px var(--neon-halo);
    white-space: nowrap;
  }
  .bold-line-art {
    position: absolute;
    inset: 0;
    width: 1200px;
    height: 1200px;
  }
  .neon-tube {
    fill: var(--neon-core);
    stroke: var(--neon-edge);
    stroke-width: 3;
    paint-order: stroke fill;
    filter:
      drop-shadow(0 0 4px var(--neon-glow))
      drop-shadow(0 0 14px var(--neon-glow))
      drop-shadow(0 0 40px var(--neon-halo));
  }
  .bold-line {
    font-family: "Montserrat", sans-serif;
    font-weight: 800;
    font-size: 212px;
  }
</style>
</head>
<body>
  <div class="sign" role="img" aria-label="Neon sign reading Light Warrior">
    <p class="script-line">Light</p>
    <svg class="bold-line-art" viewBox="0 0 1200 1200" xmlns="http://www.w3.org/2000/svg" aria-hidden="true">
      <text class="neon-tube bold-line" x="84" y="820" textLength="1043" lengthAdjust="spacingAndGlyphs">WARRIOR</text>
    </svg>
  </div>
</body>
</html>
```